Menu Redesign - Upscale Restaurant

We are looking to have our lunch and dinner menus redesigned. We are looking to elevate the signs some, no emojis. We want a clean but elevated look, please refer to Marlowe’s Dining Collective food menu and Vesper Tavola’s beverage menu. The company we’ve been using presented us with the attached menu / it’s filled with spelling and grammar errors.

Industry/Entity Type

Restaurant - Hospitality

```html
<!DOCTYPE html>
<html lang="en">
<head>
<meta charset="utf-8">
<title>Mama Lune's Creole House — Menu</title>
<link href="https://fonts.googleapis.com/css2?family=Federo&family=Oswald:wght@300;400;500&family=Roboto+Condensed:wght@400;700&display=swap" rel="stylesheet">
<style>
:root{
  --backdrop:#7b7b7b;
  --paper:#ece6de;
  --paper-deep:#e2dad0;
  --red:#df2a22;
  --ink:#141414;
  --muted:#4a4440;
  --tan:#ecd8c4;
  --tan-deep:#e6c7a7;
  --ring:#e6d3bb;
  --grid:#dcd6d0;
}
*{box-sizing:border-box;margin:0;padding:0}
html,body{width:1200px;height:979px;overflow:hidden}
body{background:var(--backdrop);position:relative;font-family:"Roboto Condensed",sans-serif;color:var(--ink)}
.page{position:absolute;top:113px;width:504px;height:753px;overflow:hidden;
  background:radial-gradient(ellipse at 30% 20%,#f3eee8 0%,var(--paper) 45%,var(--paper-deep) 100%)}
.page--food{left:66px}
.page--drinks{left:631px}
.abs{position:absolute}

.brand{position:absolute;border-radius:50%;background:#fff;border:5px solid var(--ring);display:flex;flex-direction:column;align-items:center;justify-content:center;font-family:"Federo",sans-serif;color:var(--red);text-align:center;line-height:1}
.brand__name{font-size:22px;letter-spacing:.5px}
.brand__sub{font-size:6px;letter-spacing:1px;margin-top:3px}

.tag{position:absolute;font-family:"Federo",sans-serif;color:#fff;display:flex;align-items:center;padding-left:6px;white-space:nowrap}
.tag--red{background:var(--red);clip-path:polygon(0 0,100% 0,93% 50%,100% 100%,0 100%)}
.hours__title{position:absolute;font-family:"Federo",sans-serif;font-size:30px;line-height:1;letter-spacing:.5px;white-space:nowrap}
.hours__line{position:absolute;font-family:"Oswald",sans-serif;font-weight:400;font-size:14px;white-space:nowrap;line-height:1}
.hours__line b{color:var(--red);font-weight:500}
.hours__note{position:absolute;font-family:"Roboto Condensed",sans-serif;font-size:11.5px;white-space:nowrap}

.banner{position:absolute;height:22px;display:flex;align-items:center;justify-content:center;font-family:"Oswald",sans-serif;font-weight:300;font-size:16px;color:#fff;white-space:nowrap;clip-path:polygon(0 0,100% 0,95% 50%,100% 100%,0 100%,5% 50%)}
.banner--black{background:var(--ink)}
.banner--red{background:var(--red)}

.col{position:absolute;display:flex;flex-direction:column;justify-content:space-between}
.item-name{display:flex;justify-content:space-between;font-size:6px;font-weight:700;text-transform:uppercase;line-height:1.2}
.price{color:var(--red);font-weight:700;font-size:5.6px}
.item-desc{font-size:4.6px;line-height:1.25;color:var(--muted);margin-top:1px}
.item-desc.strong{color:var(--ink)}

.panel{position:absolute;background:linear-gradient(180deg,#f0e0cf,var(--tan))}
.panel--round{border-radius:10px}
.panel__cols{position:absolute;inset:0;display:flex}
.panel__cols span{flex:1;border-right:3px solid #f3ebe2}
.panel__cols span:last-child{border-right:0}
.panel__cols .deep{background:linear-gradient(180deg,#ebcfb2,var(--tan-deep))}
.note-box{position:absolute;background:#ead7c3;border-radius:4px;padding:4px 6px;font-size:4.8px;line-height:1.3;color:var(--muted)}
.note-box b{color:var(--ink);display:block}

.sides{position:absolute;left:25px;top:693px;width:456px;height:29px;background:var(--ink);display:flex;color:#fff}
.sides__label{width:42px;background:var(--red);font-family:"Oswald",sans-serif;font-weight:300;font-size:15px;display:flex;align-items:center;justify-content:center}
.sides__grid{flex:1;display:grid;grid-template-columns:1fr 1fr 1fr .9fr 1.35fr;grid-template-rows:repeat(3,1fr);grid-auto-flow:column;padding:3px 6px;column-gap:7px}
.sides__grid p{display:flex;justify-content:space-between;gap:2px;font-size:4.3px;font-weight:700;line-height:1;white-space:nowrap}
.sides__grid .price{font-size:4.3px}

.legal{position:absolute;left:0;right:0;top:729px;text-align:center;font-size:4.6px;color:var(--muted)}

.bev{position:absolute;left:24px;top:207px;width:145px;height:150px;display:flex;flex-direction:column;justify-content:space-between}
.bev .item-name{font-weight:400}
.refill{color:var(--red);font-weight:400;font-size:5px;text-transform:none}

.spirit{position:absolute;width:92px;background:var(--grid);padding:10px 5px 4px}
.spirit__tab{position:absolute;top:-5px;left:14px;width:64px;height:9px;border-radius:2px 2px 0 0;color:#fff;font-size:5px;display:flex;align-items:center;justify-content:center;text-transform:uppercase}
.spirit__tab.red{background:var(--red)}
.spirit__tab.black{background:var(--ink)}
.spirit ul{list-style:none;columns:2;column-gap:4px}
.spirit li{font-size:4.6px;line-height:1.9;color:var(--muted);white-space:nowrap}
.spirit li::before,.dots li::before{content:"";display:inline-block;width:2.5px;height:2.5px;border-radius:50%;background:var(--red);margin-right:2.5px;vertical-align:middle}

.dots{list-style:none}
.dots li{font-size:4.8px;line-height:1.8;color:var(--muted);white-space:nowrap}

.wine{position:absolute;left:171px;top:634px;width:308px;height:46px;background:var(--grid);display:flex;padding:6px 10px;gap:14px}
.wine__group{flex:1}
.wine__head{display:flex;justify-content:space-between;font-family:"Oswald",sans-serif;font-size:10px;line-height:1.1}
.wine__head .price{font-size:8px}
.wine__head small{font-size:5px;color:var(--muted);font-family:"Roboto Condensed",sans-serif}
.wine .dots{columns:2}

.contact{position:absolute;left:24px;top:696px;width:455px;height:23px;border:1px solid #b7aea5;border-radius:12px;display:flex;align-items:center;padding:0 10px;gap:10px;font-size:8px;white-space:nowrap}
.contact__title{font-family:"Oswald",sans-serif;font-size:11px;margin-right:12px}
.contact__item{display:flex;align-items:center;gap:4px;margin-right:8px}
.contact svg{width:10px;height:10px}
</style>
</head>
<body>

<section class="page page--food">
  <div class="brand" style="left:22px;top:13px;width:138px;height:138px">
    <span class="brand__name">MAMA LUNE'S</span>
    <span class="brand__sub">CREOLE HOUSE</span>
  </div>

  <svg class="abs" style="left:200px;top:22px" width="60" height="102" viewBox="0 0 60 102" aria-hidden="true">
    <path d="M52 1 A50 50 0 0 0 52 101" fill="none" stroke="#141414" stroke-width="1.2"/>
    <path d="M54 10 A41 41 0 0 0 54 92" fill="none" stroke="#141414" stroke-width="1"/>
  </svg>
  <div class="tag tag--red" style="left:246px;top:24px;width:104px;height:20px;font-size:13px">HAPPY HOUR</div>
  <div class="hours__title" style="left:246px;top:48px">FOOD &amp; DRINKS</div>
  <div class="hours__line" style="left:246px;top:75px">MONDAY TO FRIDAY <b>3:00PM-6:00PM</b></div>
  <div class="hours__note" style="left:246px;top:89px">"Bar seats and high top tables by bar ONLY"</div>
  <div class="tag tag--red" style="left:246px;top:109px;width:76px;height:19px;font-size:13px">BRUNCH</div>
  <div class="hours__line" style="left:246px;top:131px">SATURDAY &amp; SUNDAY <b>11:00AM-3:30PM</b></div>

  <div class="banner banner--black" style="left:82px;top:157px;width:106px;height:23px">Small plates</div>

  <div class="col" style="left:24px;top:194px;width:106px;height:288px">
    <div><p class="item-name">Creole Wings<span class="price">$16</span></p><p class="item-desc strong">Fried crispy bone-in traditional wings tossed in your choice of our signature sauces: Plain, Mambo, Voodoo, Hot honey lemon pepper</p></div>
    <div><p class="item-name">Spinach Dip<span class="price">$13</span></p><p class="item-desc">Fresh chopped spinach cooked in a four cheese blend served with fresh tortilla chips. Add Jumbo Lump Crab +$6</p></div>
    <div><p class="item-name">Fried Green Tomatoes<span class="price">$13</span></p><p class="item-desc">Sliced green tomatoes seasoned in house blend battered in panko bread crumb. Add Jumbo Lump Crab +$6.</p></div>
    <div><p class="item-name">Seafood Rolls<span class="price">$18</span></p><p class="item-desc">Chopped shrimp, crab meat and cheese in a egg roll served with remoulade dipping</p></div>
    <div><p class="item-name">Steak &amp; Cheese Rolls<span class="price">$16</span></p><p class="item-desc">Philly steak, onions, peppers, and cheese in a egg roll served with chipotle mayo dipping</p></div>
    <div><p class="item-name">Bayou Rolls<span class="price">$15</span></p><p class="item-desc">Diced chicken, peppers and cheese stuffed in a egg roll served with remoulade dipping.</p></div>
    <div><p class="item-name">Fried Devil Eggs<span class="price">$13</span></p><p class="item-desc">Sweet relish, spiced whipped eggs with a choice of being topped with fresh Jumbo Lump Crab Meat or Shrimp for a upcharge.</p></div>
    <div><p class="item-name">Hot Honey Salmon Bites<span class="price">$15</span></p><p class="item-desc">Deep-fried salmon tossed in hot honey sauce</p></div>
    <div><p class="item-name">Stuffed Shrimp<span class="price">$18</span></p><p class="item-desc">Shrimp stuffed with jumbo lump crab meat coated in house batter, fried golden brown, over a bed jalapeño corn succotash.</p></div>
  </div>

  <div class="col" style="left:138px;top:194px;width:106px;height:286px">
    <div><p class="item-name">Seafood Basket<span class="price">$18</span></p><p class="item-desc">Choice of fresh battered catfish or fried golden shrimp with season fries.</p></div>
    <div><p class="item-name">New Orleans Shrimp<span class="price">$16</span></p><p class="item-desc">Creamy garlic cajun sauteed shrimp served with toasted bread</p></div>
    <div><p class="item-name">Voodoo Shrimp<span class="price">$16</span></p><p class="item-desc">Fried shrimp tossed in voodoo sauce topped with fresh jalapenos and blue cheese crumble.</p></div>
    <div><p class="item-name">Cup of Gumbo<span class="price">$15</span></p><p class="item-desc">Andouille sausage, shrimp, chicken slow cooked in a cajun broth topped with rice.</p></div>
    <div><p class="item-name">Raw Oysters<span class="price">$16</span></p><p class="item-desc">Fresh shucked blue point oysters grilled with Cajun garlic butter and four cheese blend.</p></div>
    <div><p class="item-name">Chargrilled Oysters<span class="price">$17</span></p><p class="item-desc">Fresh shucked blue point oysters grilled with Cajun garlic butter and four cheese blend</p></div>
    <div><p class="item-name">Rockefeller Oysters<span class="price">$18</span></p><p class="item-desc">Fresh shucked blue point oysters stuffed with creamy spinach and cheese.</p></div>
    <div><p class="item-name">Jambalaya Oysters<span class="price">$22</span></p><p class="item-desc">Fresh shucked blue point oysters stuffed with creamy cajun shrimp and crab</p></div>
    <div><p class="item-name">Make It A Platter<span class="price">$30</span></p><p class="item-desc strong">(Serves 3) Mix 3 of your favorite starters. (Each Seafood starter added to platter are upcharged)</p></div>
  </div>

  <div class="panel panel--round" style="left:260px;top:167px;width:220px;height:144px"></div>
  <div class="banner banner--red" style="left:322px;top:158px;width:102px">SANDWICHES</div>
  <p class="abs" style="left:260px;top:184px;width:220px;text-align:center;font-size:5px;font-weight:700">ALL SERVED WITH CAJUN</p>
  <div class="col" style="left:275px;top:200px;width:190px;height:96px">
    <div><p class="item-name">Loaded Burger<span class="price">$18</span></p><p class="item-desc">Beef patty topped with white cheddar cheese, lettuce, tomato, fried egg, and mambo sauce. Served with fries.</p></div>
    <div><p class="item-name">Mama Lune's Chicken Sandwich<span class="price">$10</span></p><p class="item-desc">Flash fried chicken dipped in honey garlic sauce, white cheddar cheese, lettuce, tomato, pickle served with fries</p></div>
    <div><p class="item-name">Crabcake Sandwich<span class="price">$25</span></p><p class="item-desc">Fresh jumbo lump crab cake, deep-fried or pan-seared. Topped with lettuce, tomato, crispy bacon, and remoulade sauce served with fries</p></div>
  </div>

  <div class="banner banner--black" style="left:317px;top:332px;width:106px">SALADS</div>
  <div class="col" style="left:258px;top:366px;width:104px;height:72px">
    <div><p class="item-name">Ceasar<span class="price">$12</span></p><p class="item-desc">Romaine, Parmesan-romano, croutons, housemade Caesar dressing.</p></div>
    <div><p class="item-name">Crispy Chicken House<span class="price">$17</span></p><p class="item-desc">Field greens, dried cranberries, cherry tomatoes, cucumbers, boiled egg, cheddar cheese, croutons, fried crispy chicken breast, and Housemade Champagne Vinaigrette</p></div>
  </div>
  <div class="col" style="left:371px;top:366px;width:105px;height:72px">
    <div><p class="item-name">Honey Caribbean Salmon<span class="price">$22</span></p><p class="item-desc">Field greens, corn off the cob, tomatoes, cucumbers, red onions, and buttermilk herb dressing</p></div>
    <div><p class="item-name">Grilled Pear &amp; Walnut<span class="price">$19</span></p><p class="item-desc">A vibrant salad of fresh greens, charred pear slices, cucumbers, red onions, cherry tomatoes, dried cranberries, walnuts, and blackened chicken.</p></div>
  </div>
  <div class="note-box" style="left:262px;top:450px;width:100px;height:29px"><b>Add Protein:</b>Shrimp +7, Salmon +12, Blackened Chicken+10, Steak +16</div>
  <div class="note-box" style="left:372px;top:450px;width:102px;height:29px"><b>Dressing Options:</b>Honey Mustard, Balsamic Vinaigrette, Ranch, Caesar, Blue Cheese</div>

  <div class="panel" style="left:0;top:499px;width:504px;height:232px">
    <div class="panel__cols"><span style="flex:1.05"></span><span class="deep" style="flex:.96"></span><span style="flex:1.15"></span></div>
  </div>
  <div class="banner banner--red" style="left:198px;top:490px;width:106px">ENTREES</div>

  <div class="col" style="left:24px;top:520px;width:126px;height:162px">
    <div><p class="item-name">Creole Herb Chicken<span class="price">$28</span></p><p class="item-desc">Creole and herb seasoned 1/2 chicken roasted tender and topped with creamy creole sauce and served with 2 sides of your choice.</p></div>
    <div><p class="item-name">Creole Salmon<span class="price">$30</span></p><p class="item-desc">Perfectly seasoned pan-seared salmon topped with creamy creole sauce served with 2 sides of your choice. Add Crab Meat +$10</p></div>
    <div><p class="item-name">Bayou Pasta<span class="price">$26</span></p><p class="item-desc">House-made cream sauce, bell peppers, tomatoes, and onions over a bed of linguine pasta topped with blackened chicken breast.</p></div>
    <div><p class="item-name">Pork Chops<span class="price">$25</span></p><p class="item-desc">Fried or grilled pork chops smothered in southern gravy served with two sides of your choice</p></div>
    <div><p class="item-name">Crab Cakes<span class="price">$MKT</span></p><p class="item-desc">2 Broiled crab cake, fresh jumbo lump crab meat, served with two sides.</p></div>
  </div>
  <div class="col" style="left:177px;top:520px;width:133px;height:162px">
    <div><p class="item-name">Mama Lune's Fried Chicken<span class="price">$23</span></p><p class="item-desc">½ chicken marinated in southern seasonings, fried golden served with two sides of your choice.</p></div>
    <div><p class="item-name">Fried Catfish<span class="price">$25</span></p><p class="item-desc">Catfish fried golden or blackened served with two sides of your choice.</p></div>
    <div><p class="item-name">Loaded Creole Pasta<span class="price">$50</span></p><p class="item-desc">Sautéed shrimp, jumbo lump crab meat, and crab leg over creamy cajun linguine.</p></div>
    <div><p class="item-name">Jambalaya Pasta<span class="price">$27</span></p><p class="item-desc">Shrimp, chicken, andouille sausage, veggies, in a Cajun cream sauce. Rice option available.</p></div>
    <div><p class="item-name">Gumbo W/ Cornbread<span class="price">$25</span></p><p class="item-desc">Rich Roux with chicken and veggies and seafood broth with andouille sausage, fresh shrimp, and scallion rice. Add Crab Leg +$10</p></div>
  </div>
  <div class="col" style="left:329px;top:520px;width:146px;height:166px">
    <div><p class="item-name">Shrimp &amp; Grits<span class="price">$28</span></p><p class="item-desc">Sautéed shrimp, onions, peppers, and tomatoes in creamy cajun sauce, over cheesy grits. Add Crab Meat +$10</p></div>
    <div><p class="item-name">Red Snapper<span class="price">$MKT</span></p><p class="item-desc">Choice of deep fried or roasted red snapper served with jambalaya stew sauce and two sides of your choice.</p></div>
    <div><p class="item-name">Oxtails<span class="price">$40</span></p><p class="item-desc">Braised oxtails with butter beans Southern-style served with your choice of two sides</p></div>
    <div><p class="item-name">Catfish &amp; Grits<span class="price">$28</span></p><p class="item-desc">Fresh wild caught blackened or fried, served over a bed of white cheddar grits topped with cajun cream sauce. Add Crab Meat +$10</p></div>
    <div><p class="item-name">Caribbean Lamb Chops<span class="price">$45</span></p><p class="item-desc">Lamb chops seasoned to perfection,topped with sweet caribbean glaze. Served with two sides of your choice.</p></div>
    <p class="item-desc">Please read menu descriptions carefully and be sure about what you are ordering. All checks will have 20% gratuity added. All parties 4+ will be on one check.</p>
  </div>

  <div class="sides">
    <div class="sides__label">SIDES</div>
    <div class="sides__grid">
      <p>CAJUN CRAB FRIES<span class="price">$18</span></p><p>SPINACH<span class="price">$7</span></p><p>LEMON HERB BROCCOLINI<span class="price">$9</span></p>
      <p>ASPARAGUS<span class="price">$9</span></p><p>FIVE CHEESE MAC<span class="price">$9</span></p><p>FRIED RICE<span class="price">$8</span></p>
      <p>SEAFOOD FRIED RICE<span class="price">$15</span></p><p>MASHED POTATOES<span class="price">$8</span></p><p>SEAFOOD MAC N CHEESE<span class="price">$15</span></p>
      <p>RED BEANS AND RICE<span class="price">$9</span></p><p>CHEESY GRITS<span class="price">$6</span></p><p>HONEY CORNBREAD<span class="price">$6</span></p>
      <p>CAJUN FRIES<span class="price">$4</span></p><p>SWEET POTATO CASSEROLE<span class="price">$7</span></p><p>COLLARD GREENS WITH SMOKED TURKEY<span class="price">$8</span></p>
    </div>
  </div>
  <p class="legal">Please alert your server if you have any food allergies. Consuming raw or undercooked meats, poultry, seafood, shellfish or eggs may increase your risk of foodborne illness.</p>
</section>

<section class="page page--drinks">
  <div class="brand" style="left:25px;top:20px;width:134px;height:134px">
    <span class="brand__name">MAMA LUNE'S</span>
    <span class="brand__sub">CREOLE HOUSE</span>
  </div>

  <svg class="abs" style="left:180px;top:23px" width="60" height="112" viewBox="0 0 60 112" aria-hidden="true">
    <path d="M56 1 A55 55 0 0 0 56 111" fill="none" stroke="#141414" stroke-width="1.2"/>
    <path d="M58 11 A45 45 0 0 0 58 101" fill="none" stroke="#141414" stroke-width="1"/>
  </svg>
  <div class="tag tag--red" style="left:227px;top:24px;width:116px;height:22px;font-size:14px">HAPPY HOUR</div>
  <div class="hours__title" style="left:226px;top:51px;font-size:32px">FOOD &amp; DRINKS</div>
  <div class="hours__line" style="left:226px;top:81px;font-size:15px">MONDAY TO FRIDAY <b>3:00PM-6:00PM</b></div>
  <div class="hours__note" style="left:226px;top:98px;font-size:12.5px">"Bar seats and high top tables by bar ONLY"</div>
  <div class="tag tag--red" style="left:227px;top:117px;width:84px;height:22px;font-size:14px">BRUNCH</div>
  <div class="hours__line" style="left:226px;top:144px;font-size:15px">SATURDAY &amp; SUNDAY <b>11:00AM-3:30PM</b></div>

  <div class="banner banner--black" style="left:24px;top:172px;width:105px">BEVERAGES</div>
  <div class="bev">
    <div><p class="item-name">Soft Drinks<span class="refill">4 (free refills)</span></p><p class="item-desc">Cola| Diet Cola| Lemon-Lime| Orange Juice| Ginger Ale| Pineapple Juice| Cranberry Juice</p></div>
    <div><p class="item-name">Creole Lemonade<br>&amp; Sweet Tea<span class="price" style="align-self:flex-end">5</span></p><p class="item-desc">Strawberry | Peach | Mango | Watermelon Kiwi | Blueberry</p></div>
    <div><p class="item-name">Ginger Beer<span class="price">4</span></p></div>
    <div><p class="item-name">Blueberry Fizz<span class="price">12</span></p><p class="item-desc">Blueberry, lime, ginger beer.</p></div>
    <div><p class="item-name">Pineapple Punch<span class="price">12</span></p><p class="item-desc">Orange &amp; pineapple juice,mai tai, peach, fresh lime.</p></div>
    <div><p class="item-name">Still Spring Water<span class="price">5</span></p></div>
    <div><p class="item-name">Sparkling Mineral Water<span class="price">5</span></p></div>
  </div>

  <div class="banner banner--red" style="left:297px;top:173px;width:104px">SPIRITS</div>
  <div class="spirit" style="left:196px;top:214px;height:67px"><span class="spirit__tab red">Bourbon &amp; Whiskey</span>
    <ul><li>Oakridge</li><li>Cedar Hollow</li><li>Millbrook</li><li>Millbrook Rye</li><li>Harbor Apple</li><li>Hollis Lane</li><li>Fieldstone</li><li>Old Ferris</li><li>Harbor Royal</li><li>Kerrigan</li><li>Jasper Barrel</li></ul></div>
  <div class="spirit" style="left:291px;top:214px;height:67px"><span class="spirit__tab black">Scotch</span>
    <ul style="columns:1"><li>Loch Varra Black</li><li>Craigmoor 12</li></ul></div>
  <div class="spirit" style="left:386px;top:214px;height:67px"><span class="spirit__tab red">Vodka</span>
    <ul><li>Northfield</li><li>Stillhouse One</li><li>Prairie Line</li><li>White Heron</li><li>Aurelle</li><li style="padding-left:5px">Double Espresso</li></ul></div>
  <div class="spirit" style="left:196px;top:299px;height:56px"><span class="spirit__tab black">Gin</span>
    <ul><li>Harbor Blue</li><li>Wexley's</li><li>Thornbury</li><li>Violet Crown</li></ul></div>
  <div class="spirit" style="left:291px;top:299px;height:56px"><span class="spirit__tab red">Tequila</span>
    <ul><li>Casa Solana</li><li>Puerta Roja</li><li>Sierra Lumbre</li><li>Tres Lunas</li><li>Agave Real</li><li>Puerta Roja 1950</li><li>Valle Claro</li></ul></div>
  <div class="spirit" style="left:386px;top:299px;height:56px"><span class="spirit__tab black">Rum</span>
    <ul style="columns:1"><li>Isla Verde</li><li>Commodore Reef Spiced</li><li>Dark Harbor</li></ul></div>

  <div class="panel" style="left:0;top:391px;width:504px;height:190px">
    <div class="panel__cols"><span style="flex:1.1"></span><span class="deep" style="flex:1"></span><span style="flex:1.1"></span></div>
  </div>
  <div class="banner banner--black" style="left:157px;top:381px;width:190px;height:21px">SPECILAILTY COCKTAILS</div>

  <div class="col" style="left:24px;top:412px;width:133px;height:150px">
    <div><p class="item-name">Mama Lune's Hurricane<span class="price">$16</span></p><p class="item-desc">Dark rum light rum, passion fruit punch lime juice, orange juice, grenadine.</p></div>
    <div><p class="item-name">Tsunami<span class="price">$16</span></p><p class="item-desc">Blanco tequila, pineapple, orange, passionfruit, blue curacao topped with dark tequila.</p></div>
    <div><p class="item-name">Secrets<span class="price">$15</span></p><p class="item-desc">Secret blend of 3 rums, tropical punch, and fresh lime</p></div>
    <div><p class="item-name">Smoked In Fashion<span class="price">$18</span></p><p class="item-desc">Bourbon, cubed sugar, black cherry, orange and cherry bitters.</p></div>
    <div><p class="item-name">Smoked Tequila Old Fashion<span class="price">$18</span></p><p class="item-desc">Aged tequila, orange liqueur, agave nectar, peach bitters, fresh orange peel.</p></div>
  </div>
  <div class="col" style="left:177px;top:412px;width:128px;height:150px">
    <div><p class="item-name">Miskir<span class="price">$17</span></p><p class="item-desc">Tequila, orange liqueur, blackberry, pineapple, cranberry, lemon juice.</p></div>
    <div><p class="item-name">Blackberry French<span class="price">$15</span></p><p class="item-desc">Violet Crown Gin, lemonade champagne, blackberries, white flower.</p></div>
    <div><p class="item-name">Margarita or Lemon Drop Flight<span class="price">$20</span></p><p class="item-desc">Traditional, Strawberry, Blueberry, Passionfruit, On the rocks</p></div>
    <div><p class="item-name">Lousiana Tea<span class="price">$27</span></p><p class="item-desc">Old Ferris whiskey, honey mint syrup, fresh lemonade.</p></div>
    <div><p class="item-name">Pink Lady<span class="price">$15</span></p><p class="item-desc">Tequila, orange liqueur, lime, stawberry-kiwi, agave.</p></div>
  </div>
  <div class="col" style="left:329px;top:412px;width:145px;height:160px">
    <div><p class="item-name">Creole Island<span class="price">$19</span></p><p class="item-desc">Orange liqueur, cognac, tropical punch.</p></div>
    <div><p class="item-name">Becky Sangria<span class="price">$18</span></p><p class="item-desc">Red wine blend, cognac, tropical fruit punch, and frozen popsicle.</p></div>
    <div><p class="item-name">Pineapple-Gria<span class="price">$18</span></p><p class="item-desc">White sparkling wine, rum, pineapple punch.</p></div>
    <div><p class="item-name">Peach Please<span class="price">$16</span></p><p class="item-desc">Vodka, peach nectar, champagne</p></div>
    <div><p class="item-name">Toasted Marshmallow<br>Espresso Martini<span class="price" style="align-self:flex-end">$16</span></p><p class="item-desc">Toasted marshmallow, espresso, vodka, cream, white chocolate liqueur</p></div>
    <div><p class="item-name">Lune's Passion<span class="price">$18</span></p><p class="item-desc">Cognac VSOP, orange liqueur, lemon juice, passionfruit.</p></div>
  </div>

  <div class="banner banner--black" style="left:24px;top:606px;width:105px">BEERS</div>
  <div class="wine__head abs" style="left:24px;top:636px;width:126px"><span>BOTTLE</span><span class="price">7</span></div>
  <ul class="dots abs" style="left:26px;top:649px;columns:2;width:110px">
    <li>Prairie Light</li><li>Island Lager</li><li>Harvest Wheat</li><li>Playa Clara</li><li>Orchard Row Cider</li><li>Lowland Pilsner</li><li>Seasonal IPA</li>
  </ul>

  <div class="banner banner--red" style="left:170px;top:606px;width:149px">WINE AND BUBBLY</div>
  <div class="wine__head abs" style="left:326px;top:610px;width:153px"><span>THE GLASS</span><span class="price">10</span></div>
  <div class="wine">
    <div class="wine__group"><div class="wine__head"><span>REDS</span><span class="price">10</span></div><ul class="dots"><li>Cabernet</li><li>Merlot</li><li>Pinot Noir</li><li>Sweet Red Blend</li></ul></div>
    <div class="wine__group"><div class="wine__head"><span>WHITE</span><span class="price">10</span></div><ul class="dots"><li>Moscato</li><li>Pinot Grigio</li><li>Sauvignon Blanc</li><li>Chardonnay</li></ul></div>
    <div class="wine__group"><div class="wine__head"><span>BUBBLY <small>(by the glass)</small></span></div><ul class="dots"><li>Prosecco 13</li><li>Brut 9</li></ul></div>
  </div>

  <div class="contact">
    <span class="contact__title">CONTACT US</span>
    <span class="contact__item"><svg viewBox="0 0 10 10" aria-hidden="true"><circle cx="5" cy="5" r="5" fill="#df2a22"/><path d="M3 2.6c.3-.3.7-.2.8.1l.4.8c.1.3 0 .5-.2.6l-.3.2c.3.7.8 1.2 1.5 1.5l.2-.3c.1-.2.4-.3.6-.2l.8.4c.3.1.4.5.1.8l-.4.4c-.4.4-2 .1-3.1-1S2.2 3.4 2.6 3z" fill="#fff"/></svg>(555)-014-2270</span>
    <span class="contact__item"><svg viewBox="0 0 10 10" aria-hidden="true"><circle cx="5" cy="5" r="5" fill="#df2a22"/><rect x="2.5" y="3.2" width="5" height="3.6" fill="none" stroke="#fff" stroke-width=".7"/><path d="M2.5 3.3 5 5.2 7.5 3.3" fill="none" stroke="#fff" stroke-width=".7"/></svg>hello@mamalunescreole.com</span>
    <span class="contact__item"><svg viewBox="0 0 10 10" aria-hidden="true"><circle cx="5" cy="5" r="5" fill="#df2a22"/><circle cx="5" cy="5" r="2.6" fill="none" stroke="#fff" stroke-width=".6"/><path d="M2.4 5h5.2M5 2.4c-1.2 1.4-1.2 3.8 0 5.2M5 2.4c1.2 1.4 1.2 3.8 0 5.2" fill="none" stroke="#fff" stroke-width=".5"/></svg>www.mamalunescreole.com</span>
  </div>
  <p class="legal">Please alert your server if you have any food allergies. Consuming raw or undercooked meats, poultry, seafood, shellfish or eggs may increase your risk of foodborne illness.</p>
</section>

</body>
</html>
```